R. Talmont Realty, Inc business card (2 sided), letterhead (1 sided) & #10 envelope (1 sided)

business card of standard size utilizing the attached logo. Side one with logo, Owen Talmont (my name), President / Broker (title), 805-317-2684 (phone), www.rtalmontrealty.example (website), 1726 Harlow Avenue, Suite 4052 San Luis Obiso, CA 93628 (business address) owen.rtalmontrealty@mailbox.example (e-mail address),
Side two - Log

Letterhead and #10 envelope in the same theme
Updates

Project Deadline Extended
Reason: I think a 2 day deadline may be a bit ambitious on my part. I have extended the deadline to 4 days. Thanks!

Industry/Entity Type

Business

```html
<!DOCTYPE html>
<html lang="en">
<head>
<meta charset="utf-8">
<title>R. Talmont Realty, Inc — Business Card</title>
<link rel="stylesheet" href="https://fonts.googleapis.com/css2?family=Noticia+Text:wght@400;700&family=Open+Sans:wght@400;600&display=swap">
<style>
  :root {
    --backdrop: #e9e6e1;
    --card: #ffffff;
    --card-edge: #5a5a5a;
    --brand-blue: #1d6c8e;
    --band-dark: #0f4f6c;
    --band-light: #3f8fb0;
    --rule: #3a3f44;
    --ink: #2b2b2b;
    --white: #ffffff;
  }
  * { box-sizing: border-box; margin: 0; padding: 0; }
  html, body {
    width: 1200px;
    height: 1182px;
    overflow: hidden;
    background: var(--backdrop);
  }
  .canvas {
    position: relative;
    width: 1200px;
    height: 1182px;
  }
  .card {
    position: absolute;
    width: 910px;
    height: 519px;
    background: var(--card);
    border: 1.5px solid var(--card-edge);
  }
  .card--front { left: 245px; top: 41px; }
  .card--back  { left: 41px;  top: 612px; }

  .brand {
    position: absolute;
    left: 0;
    right: 0;
    display: flex;
    align-items: center;
    justify-content: center;
    gap: 16px;
    font-family: "Noticia Text", Georgia, serif;
    font-weight: 400;
    color: var(--brand-blue);
    letter-spacing: 0.5px;
  }
  .brand__mark {
    width: 22px;
    height: 22px;
    background: var(--brand-blue);
  }
  .card--front .brand { top: 100px; font-size: 52px; }
  .card--back  .brand { top: 185px; font-size: 56px; }

  .name-band {
    position: absolute;
    left: 0;
    right: 0;
    top: 296px;
    height: 70px;
    border-top: 3px solid var(--rule);
    border-bottom: 3px solid var(--rule);
  }
  .name-band__fill {
    position: absolute;
    left: 0;
    right: 0;
    top: 7px;
    height: 50px;
    background: linear-gradient(90deg, var(--band-dark) 0%, var(--band-light) 30%, var(--band-light) 62%, var(--band-dark) 100%);
    display: flex;
    align-items: center;
    justify-content: center;
    color: var(--white);
    font-family: "Noticia Text", Georgia, serif;
  }
  .name-band__name { font-weight: 700; font-size: 31px; }
  .name-band__title { font-weight: 400; font-size: 27px; margin-left: 8px; }

  .contact {
    position: absolute;
    left: 0;
    right: 0;
    display: flex;
    align-items: center;
    justify-content: center;
    font-family: "Open Sans", Arial, sans-serif;
    color: var(--ink);
  }
  .contact--phone { top: 393px; font-size: 26px; gap: 8px; }
  .contact--online { top: 449px; font-size: 20px; gap: 8px; }
  .contact__icon { width: 20px; height: 20px; flex: none; }
  .contact--phone .contact__icon { width: 24px; height: 24px; }
  .contact__gap { width: 14px; }

  .back-web {
    position: absolute;
    left: 0;
    right: 0;
    top: 432px;
    text-align: center;
    font-family: "Open Sans", Arial, sans-serif;
    font-size: 29px;
    letter-spacing: 4px;
    color: var(--ink);
  }
</style>
</head>
<body>
<main class="canvas">

  <section class="card card--front" aria-label="Business card front">
    <div class="brand">
      <span class="brand__mark"></span>
      <span class="brand__name">R. Talmont Realty, Inc</span>
    </div>

    <div class="name-band">
      <div class="name-band__fill">
        <span class="name-band__name">Owen Talmont,</span>
        <span class="name-band__title">President / Broker</span>
      </div>
    </div>

    <div class="contact contact--phone">
      <svg class="contact__icon" viewBox="0 0 24 24" aria-hidden="true">
        <circle cx="12" cy="12" r="11" fill="var(--brand-blue)"/>
        <path d="M8.5 6.5c.6-.4 1.3-.3 1.7.3l1 1.6c.3.5.2 1.1-.2 1.5l-.7.6c.5 1.3 1.4 2.4 2.6 3.1l.7-.6c.4-.4 1-.4 1.5-.1l1.6 1c.6.4.7 1.2.2 1.7l-.7.8c-.9.9-4 .1-6.2-2.3-2.3-2.5-2.9-5.5-2-6.3z" fill="var(--white)"/>
      </svg>
      <span>805-317-2684</span>
    </div>

    <div class="contact contact--online">
      <svg class="contact__icon" viewBox="0 0 20 20" aria-hidden="true">
        <circle cx="10" cy="10" r="9.5" fill="var(--brand-blue)"/>
        <rect x="5" y="6.5" width="10" height="7" fill="var(--white)"/>
        <path d="M5 6.5l5 4 5-4" fill="none" stroke="var(--brand-blue)" stroke-width="1.2"/>
      </svg>
      <span>owen.rtalmontrealty@mailbox.example</span>
      <span class="contact__gap"></span>
      <svg class="contact__icon" viewBox="0 0 20 20" aria-hidden="true">
        <circle cx="10" cy="10" r="9.5" fill="var(--brand-blue)"/>
        <circle cx="10" cy="10" r="6" fill="none" stroke="var(--white)" stroke-width="1.2"/>
        <ellipse cx="10" cy="10" rx="2.6" ry="6" fill="none" stroke="var(--white)" stroke-width="1.1"/>
        <path d="M4 10h12" stroke="var(--white)" stroke-width="1.1"/>
      </svg>
      <span>www.rtalmontrealty.example</span>
    </div>
  </section>

  <section class="card card--back" aria-label="Business card back">
    <div class="brand">
      <span class="brand__mark"></span>
      <span class="brand__name">R. Talmont Realty, Inc</span>
    </div>
    <p class="back-web">www.rtalmontrealty.example</p>
  </section>

</main>
</body>
</html>
```